Sandwich Board and Poster design promoting a medical aesthetic clinic

I am looking for a clean, modern and relaxing design promoting a medical physician-led aesthetic clinic.
Services offered are neuromodulator treatment (Dyneline) and Dermal Fillers.
Logo must be included.
Use the tag line "Refresh your look, revive your spirit."
Address is 204-205 27361 93 Ave, Surrey, K7P 2R4
604-555-0172
email - info@brightmoorskin.ca
www.brightmoorskin.ca

```html
<!DOCTYPE html>
<html lang="en">
<head>
<meta charset="utf-8">
<title>Brightmoor Skin – Refresh Your Look Poster</title>
<link href="https://fonts.googleapis.com/css2?family=Italiana&family=Poppins:wght@400;500;600;700;800&display=swap" rel="stylesheet">
<style>
  :root {
    --navy-deep: #0f2748;
    --navy-mid: #1a3a64;
    --blue-glow: #2f6497;
    --gold: #e0b82c;
    --gold-ring: #9a8a4a;
    --white: #ffffff;
    --ink: #111a2a;
    --ink-blue: #1d3556;
    --stage: #c8c8c8;
  }
  * { box-sizing: border-box; margin: 0; padding: 0; }
  html, body { width: 1200px; height: 1200px; overflow: hidden; }
  body { background: var(--stage); position: relative; font-family: "Poppins", sans-serif; }

  .poster {
    position: absolute; left: 233px; top: 50px;
    width: 733px; height: 1100px; overflow: hidden;
    background: radial-gradient(ellipse 70% 45% at 55% 50%, var(--blue-glow) 0%, var(--navy-mid) 55%, var(--navy-deep) 100%);
    color: var(--white);
  }
  .abs { position: absolute; }

  .headline-top {
    top: 62px; left: 0; width: 100%; text-align: center;
    font-weight: 500; font-size: 36px; letter-spacing: 0.32em; text-indent: 0.32em;
  }
  .headline-main {
    top: 100px; left: 0; width: 100%; text-align: center;
    font-weight: 800; font-size: 86px; line-height: 1.1; letter-spacing: -2px; color: var(--gold);
  }
  .headline-sub {
    top: 188px; left: 0; width: 100%; text-align: center;
    font-family: "Italiana", serif; font-size: 66px; line-height: 1.2; letter-spacing: -1px;
  }
  .divider-line { top: 278px; left: 127px; width: 478px; height: 1px; background: rgba(255,255,255,0.35); }
  .divider-accent { top: 275px; left: 323px; width: 87px; height: 7px; border-radius: 4px; background: var(--gold); }

  .services-title {
    top: 315px; left: 0; width: 100%; text-align: center;
    font-size: 33px; letter-spacing: 0.12em; text-indent: 0.12em; font-weight: 400;
  }
  .services-title strong { font-weight: 700; }

  .service-photo {
    width: 186px; height: 186px; border-radius: 50%;
    border: 6px solid var(--gold-ring);
  }
  .service-photo--neuro { left: 88px; top: 378px; background: linear-gradient(135deg, #a9d3ea 0%, #c89a7d 45%, #5a3b28 100%); }
  .service-photo--filler { left: 88px; top: 638px; background: linear-gradient(160deg, #f2e9e4 0%, #e8c0ae 55%, #4e63c8 100%); }

  .service-label {
    left: 40px; width: 282px; text-align: center;
    font-size: 21px; line-height: 1.28; font-weight: 500;
  }
  .service-label--neuro { top: 570px; }
  .service-label--filler { top: 830px; }

  .hero-photo {
    left: 307px; top: 379px; width: 426px; height: 580px;
    border-radius: 200px 180px 0 0;
    background: linear-gradient(200deg, #3a2a22 0%, #d9b19a 35%, #4e8f2f 60%, #d95aa8 85%, #e9e4e1 100%);
    opacity: 0.9;
  }

  .footer-wave { left: 0; top: 900px; width: 733px; height: 200px; }

  .phone-pill {
    left: 177px; top: 891px; width: 379px; height: 44px; border-radius: 22px;
    background: var(--gold); display: flex; align-items: center; padding-left: 6px;
    box-shadow: 0 10px 14px -6px rgba(0,0,0,0.35);
  }
  .phone-pill__icon { width: 32px; height: 32px; border-radius: 50%; background: var(--white); display: flex; align-items: center; justify-content: center; }
  .phone-pill__number {
    margin-left: 20px; font-weight: 700; font-size: 29px; letter-spacing: 0.17em; color: var(--ink);
  }

  .brand-name {
    left: 72px; top: 1000px; width: 200px; text-align: center;
    font-weight: 500; font-size: 22px; line-height: 1.25; letter-spacing: 0.22em; color: var(--ink);
  }

  .contact-row { left: 278px; display: flex; align-items: center; color: var(--ink); font-weight: 500; font-size: 17px; }
  .contact-row svg { flex: none; margin-right: 12px; }
  .contact-row--email { top: 960px; }
  .contact-row--address { top: 997px; }
  .website {
    left: 280px; top: 1024px; font-weight: 700; font-size: 25px; letter-spacing: 0.12em; color: var(--ink);
  }
  .website span { color: var(--ink-blue); }
</style>
</head>
<body>
  <main class="poster">
    <div class="abs headline-top">REFRESH</div>
    <div class="abs headline-main">YOUR LOOK</div>
    <div class="abs headline-sub">REVIVE YOUR SPIRIT</div>
    <div class="abs divider-line"></div>
    <div class="abs divider-accent"></div>

    <div class="abs services-title"><strong>SERVICES</strong> WE OFFER</div>

    <div class="abs hero-photo" role="img" aria-label="Photo of a woman receiving a chin injection from gloved hands, with a green monstera leaf behind her"></div>

    <div class="abs service-photo service-photo--neuro" role="img" aria-label="Photo of a forehead neuromodulator injection"></div>
    <div class="abs service-label service-label--neuro">Neuromodulator<br>treatment (Dyneline)</div>

    <div class="abs service-photo service-photo--filler" role="img" aria-label="Photo of a lip dermal filler treatment"></div>
    <div class="abs service-label service-label--filler">Dermal Fillers</div>

    <svg class="abs footer-wave" viewBox="0 0 733 200" preserveAspectRatio="none" aria-hidden="true">
      <path d="M0 44 Q366 -6 733 44 L733 200 L0 200 Z" fill="#ffffff"/>
    </svg>

    <div class="abs phone-pill">
      <div class="phone-pill__icon">
        <svg width="18" height="18" viewBox="0 0 24 24" aria-hidden="true">
          <path d="M6.6 10.8a15.1 15.1 0 0 0 6.6 6.6l2.2-2.2a1 1 0 0 1 1-.25 11.4 11.4 0 0 0 3.6.57 1 1 0 0 1 1 1V20a1 1 0 0 1-1 1A17 17 0 0 1 3 4a1 1 0 0 1 1-1h3.5a1 1 0 0 1 1 1c0 1.25.2 2.45.57 3.6a1 1 0 0 1-.25 1z" fill="#111a2a"/>
        </svg>
      </div>
      <div class="phone-pill__number">604-555-0172</div>
    </div>

    <div class="abs brand-name">BRIGHTMOOR<br>SKIN</div>

    <div class="abs contact-row contact-row--email">
      <svg width="22" height="16" viewBox="0 0 22 16" aria-hidden="true">
        <rect x="0" y="0" width="22" height="16" rx="1.5" fill="#1d3556"/>
        <path d="M1 1.5 L11 9 L21 1.5" stroke="#ffffff" stroke-width="1.8" fill="none"/>
        <path d="M1 15 L8 7.5 M21 15 L14 7.5" stroke="#ffffff" stroke-width="1.4"/>
      </svg>
      info@brightmoorskin.ca
    </div>
    <div class="abs contact-row contact-row--address">
      <svg width="18" height="24" viewBox="0 0 18 24" aria-hidden="true" style="margin-left:2px">
        <path d="M9 0a9 9 0 0 0-9 9c0 6.5 9 15 9 15s9-8.5 9-15a9 9 0 0 0-9-9z" fill="#1d3556"/>
        <circle cx="9" cy="9" r="3.4" fill="#ffffff"/>
      </svg>
      204-205 27361 93 Ave, Surrey, K7P 2R4
    </div>
    <div class="abs website">www.<span>brightmoorskin</span>.ca</div>
  </main>
</body>
</html>
```